Upmarket Dessert Lounge needs a Business Card Design

We are an upmarket dessert lounge needing a business card to match our image.

We want something that is simple yet beautiful, feminine, classy, sophisticated and elegant. We want it to stand out and don't mind if it is bold.

The design should include our logo and colours of red or maroon with gold highlights. We don't mind if black is used.

Marlow & Quince

Target Market(s)

For those who like to indulge or treat themselves and give in to their temptations on good quality desserts.

Industry/Entity Type

Business

Requirements
Must have
• Must include our logo and our name

Marlow & Quince

M & Q

```html
<!DOCTYPE html>
<html lang="en">
<head>
<meta charset="UTF-8">
<title>Marlow &amp; Quince — Business Card</title>
<link rel="stylesheet" href="https://fonts.googleapis.com/css2?family=Libre+Baskerville:wght@400;700&display=swap">
<style>
  :root {
    --backdrop: #f1e5e6;
    --maroon: #6a1d1e;
    --gold: #f3c27c;
    --gold-soft: rgba(243, 194, 124, 0.55);
    --gold-fade: rgba(243, 194, 124, 0);
    --cream: #fbeee0;
  }
  * { box-sizing: border-box; margin: 0; padding: 0; }
  html, body {
    width: 1200px;
    height: 951px;
    overflow: hidden;
  }
  body {
    position: relative;
    background: var(--backdrop);
    font-family: "Libre Baskerville", Georgia, serif;
  }
  .card {
    position: absolute;
    width: 620px;
    height: 354px;
    background: var(--maroon);
    border-radius: 26px;
    overflow: hidden;
    box-shadow: 0 6px 18px rgba(60, 20, 20, 0.18);
  }
  .card--front { left: 100px; top: 90px; }
  .card--back  { left: 480px; top: 500px; }

  .ornament {
    position: absolute;
    display: block;
  }
  .ornament--front-corner {
    right: 0; top: 0;
    width: 250px; height: 150px;
    background: radial-gradient(ellipse at top right, var(--gold-soft), var(--gold-fade) 72%);
  }
  .ornament--back-top {
    right: 0; top: 0;
    width: 190px; height: 170px;
    background: radial-gradient(ellipse at top right, var(--gold-soft), var(--gold-fade) 72%);
  }
  .ornament--back-bottom {
    left: 0; bottom: 0;
    width: 150px; height: 240px;
    background: radial-gradient(ellipse at bottom left, var(--gold-soft), var(--gold-fade) 72%);
  }

  .wordmark {
    position: absolute;
    color: var(--gold);
    font-weight: 400;
    white-space: nowrap;
    text-align: center;
  }
  .wordmark--full {
    left: 0; top: 128px;
    width: 500px;
    font-size: 30px;
    letter-spacing: 2px;
  }
  .wordmark--initials {
    left: 30px; top: 48px;
    width: 180px;
    font-size: 42px;
    letter-spacing: 1px;
  }

  .website {
    position: absolute;
    left: 0; top: 268px;
    width: 500px;
    text-align: center;
    color: var(--cream);
    font-size: 17px;
    font-weight: 700;
    letter-spacing: 1.5px;
  }

  .contact {
    position: absolute;
    right: 44px; top: 178px;
    text-align: right;
    color: var(--cream);
    font-weight: 700;
  }
  .contact-name {
    color: var(--gold);
    font-size: 22px;
    margin-bottom: 12px;
  }
  .contact-address {
    font-size: 14px;
    line-height: 1.4;
    font-style: normal;
    margin-bottom: 14px;
  }
  .contact-line {
    font-size: 14px;
    line-height: 1.6;
  }
  .contact-line .accent { color: var(--gold); }
</style>
</head>
<body>
  <section class="card card--front" aria-label="Business card front">
    <span class="ornament ornament--front-corner" role="img" aria-label="Gold flourish ornament in the top right corner"></span>
    <div class="wordmark wordmark--full">MARLOW &amp; QUINCE</div>
    <p class="website">www.marlow&amp;quince.com</p>
  </section>

  <section class="card card--back" aria-label="Business card back">
    <span class="ornament ornament--back-top" role="img" aria-label="Gold flourish ornament in the top right corner"></span>
    <span class="ornament ornament--back-bottom" role="img" aria-label="Gold flourish ornament in the bottom left corner"></span>
    <div class="wordmark wordmark--initials">M&amp;Q</div>
    <div class="contact">
      <p class="contact-name">Marlow &amp; Quince</p>
      <address class="contact-address">48 Larkspur Lane, Suite 210<br>Brookhaven, Ohio 44012</address>
      <p class="contact-line">330-555-0148</p>
      <p class="contact-line">info@<span class="accent">marlow&amp;quince</span>.com</p>
    </div>
  </section>
</body>
</html>
```